Business Card Design Project

I require a business card with the following information on them for various different people;
name
m:
f:
e:
I have a logo already and will attached that. We are in the construction industry. I require something clean and simple but eye catching at the same time. You can use another colour with our logo if you like and you can style the logo as well if you wish. I am open.
Also it needs to be front and back design.
Industry/Entity Type
Construction
Requirements
Must have
- Logo, name, mobile, fax and email address.
Front and back design

```html
<!DOCTYPE html>
<html lang="en">
<head>
<meta charset="utf-8">
<title>Business Card Options</title>
<link rel="stylesheet" href="https://fonts.googleapis.com/css2?family=Open+Sans:wght@300;400;600;700&display=swap">
<style>
  :root {
    --backdrop: #e8e1d8;
    --paper: #ffffff;
    --green-deep: #3a7424;
    --green-mid: #4f8f2c;
    --green-light: #a9cf4f;
    --green-logo: #4aa83a;
    --silver: #c9c9cd;
    --ink-soft: #5a5a5a;
    --ink-faint: #b9c9ae;
    --ink-dark: #1f2a1a;
    --label: #111111;
  }
  * { box-sizing: border-box; margin: 0; padding: 0; }
  html, body { width: 1200px; height: 1133px; overflow: hidden; }
  body {
    background: var(--backdrop);
    font-family: "Open Sans", Arial, sans-serif;
    position: relative;
  }
  .option-label {
    position: absolute;
    left: 0; width: 1200px;
    text-align: center;
    font-weight: 700;
    font-size: 37px;
    line-height: 1;
    color: var(--label);
  }
  .card {
    position: absolute;
    width: 514px; height: 293px;
    overflow: hidden;
  }
  .card-front { left: 47px; background: var(--paper); }
  .card-back {
    left: 640px;
    background: radial-gradient(ellipse 220px 170px at 48% 55%, var(--green-light) 0%, #7fb23a 35%, var(--green-mid) 70%, var(--green-deep) 100%);
  }
  .front-band {
    position: absolute;
    left: 0; right: 0; top: 220px; bottom: 0;
    background: linear-gradient(90deg, #a9cf4f 0%, #6fa836 45%, var(--green-deep) 100%);
    border-top: 6px solid var(--silver);
  }
  .brand {
    position: absolute;
    left: 38px; top: 40px;
    display: flex; align-items: center; gap: 12px;
  }
  .brand-mark { width: 26px; height: 26px; background: var(--green-logo); }
  .brand-name {
    font-weight: 300;
    font-size: 34px;
    line-height: 1.2;
    color: var(--green-logo);
    white-space: nowrap;
  }
  .person {
    position: absolute;
    left: 37px; top: 192px;
    font-size: 16px; line-height: 1.2;
    color: var(--ink-soft);
  }
  .person .name { font-weight: 700; }
  .person .title { font-size: 12.5px; font-weight: 400; }
  .contacts {
    position: absolute;
    right: 24px; top: 228px;
    list-style: none;
    font-size: 12.5px;
    color: #ffffff;
  }
  .contacts li {
    display: flex; justify-content: flex-end; align-items: center;
    gap: 11px; height: 20px;
  }
  .contacts svg { width: 10px; height: 10px; fill: currentColor; }
  .contacts.is-faint { color: var(--ink-faint); }
  .contacts.is-dark { color: var(--ink-dark); }
  .back-name {
    position: absolute; left: 0; right: 0; top: 116px;
    text-align: center;
    font-weight: 300;
    font-size: 44px;
    line-height: 1.2;
    white-space: nowrap;
  }
  .back-name.is-white { color: #ffffff; }
  .back-name.is-dark { color: #3a3a3a; }
  .back-name.is-green { color: #35a63a; }
</style>
</head>
<body>

  <div class="option-label" style="top:12px">Option_1</div>
  <div class="option-label" style="top:385px">Option_2</div>
  <div class="option-label" style="top:761px">Option_3</div>

  <section class="card card-front" style="top:66px">
    <div class="front-band" role="img" aria-label="Green and silver wave band"></div>
    <div class="brand"><span class="brand-mark"></span><span class="brand-name">Stonefield Builders</span></div>
    <p class="person"><span class="name">Your Name</span> <span class="title">/ Title</span></p>
    <ul class="contacts">
      <li>123-456-7890 <svg viewBox="0 0 10 10"><circle cx="5" cy="5" r="4.2" fill="none" stroke="currentColor" stroke-width="1.2"/><path d="M3.5,3 L4.5,3 L5,6.5 L6.5,7 L6.5,7.5 L5,7.5 Z"/></svg></li>
      <li>123-456-7890 <svg viewBox="0 0 10 10"><rect x="3" y="1" width="4" height="3"/><rect x="1" y="4" width="8" height="5"/></svg></li>
      <li>name@website.com <svg viewBox="0 0 10 10"><rect x="1" y="2.5" width="8" height="5.5"/></svg></li>
    </ul>
  </section>
  <section class="card card-back" style="top:66px">
    <p class="back-name is-white">Stonefield Builders</p>
  </section>

  <section class="card card-front" style="top:439px">
    <div class="front-band" role="img" aria-label="Green and silver wave band"></div>
    <div class="brand"><span class="brand-mark"></span><span class="brand-name">Stonefield Builders</span></div>
    <p class="person"><span class="name">Your Name</span> <span class="title">/ Title</span></p>
    <ul class="contacts is-faint">
      <li>123-456-7890 <svg viewBox="0 0 10 10"><circle cx="5" cy="5" r="4.2" fill="none" stroke="currentColor" stroke-width="1.2"/><path d="M3.5,3 L4.5,3 L5,6.5 L6.5,7 L6.5,7.5 L5,7.5 Z"/></svg></li>
      <li>123-456-7890 <svg viewBox="0 0 10 10"><rect x="3" y="1" width="4" height="3"/><rect x="1" y="4" width="8" height="5"/></svg></li>
      <li>name@website.com <svg viewBox="0 0 10 10"><rect x="1" y="2.5" width="8" height="5.5"/></svg></li>
    </ul>
  </section>
  <section class="card card-back" style="top:439px">
    <p class="back-name is-dark">Stonefield Builders</p>
  </section>

  <section class="card card-front" style="top:814px">
    <div class="front-band" role="img" aria-label="Green and silver wave band"></div>
    <div class="brand"><span class="brand-mark"></span><span class="brand-name">Stonefield Builders</span></div>
    <p class="person"><span class="name">Your Name</span> <span class="title">/ Title</span></p>
    <ul class="contacts is-dark">
      <li>123-456-7890 <svg viewBox="0 0 10 10"><circle cx="5" cy="5" r="4.2" fill="none" stroke="currentColor" stroke-width="1.2"/><path d="M3.5,3 L4.5,3 L5,6.5 L6.5,7 L6.5,7.5 L5,7.5 Z"/></svg></li>
      <li>123-456-7890 <svg viewBox="0 0 10 10"><rect x="3" y="1" width="4" height="3"/><rect x="1" y="4" width="8" height="5"/></svg></li>
      <li>name@website.com <svg viewBox="0 0 10 10"><rect x="1" y="2.5" width="8" height="5.5"/></svg></li>
    </ul>
  </section>
  <section class="card card-back" style="top:814px">
    <p class="back-name is-green">Stonefield Builders</p>
  </section>

</body>
</html>
```